New Business Cards for Tormin Group

We need a new Business Card to compliment our new logo. We are a vibrant design, manufacture and install business providing recreation areas, public parks and Municipal spaces. We want business cards that are classy, modern and clean.

We have recently changed our logo, and are celebrating our 40th anniversary. We want business cards with a new modern design to reflect our status.

Target Market(s)

Customers

Contact Information for Business Card

We need all the details of our 3 offices as per the business card attached. Please disregard the old logo on the business card, the other three files show our new logo.

Requirements
Must have
• All info as per attached business card but with new logo.
Nice to have

```html
<!DOCTYPE html>
<html lang="en">
<head>
<meta charset="utf-8">
<title>Tormin Group – Business Card</title>
<link href="https://fonts.googleapis.com/css2?family=Lato:wght@400;700&display=swap" rel="stylesheet">
<style>
  :root {
    --backdrop: #5e5e5e;
    --card: #ffffff;
    --accent: #e8303a;
    --ink: #3a3a3a;
    --muted: #6f6f6f;
    --rule: #5a5a5a;
    --band: #4a4a4c;
  }
  * { margin: 0; padding: 0; box-sizing: border-box; }
  html, body {
    width: 1200px; height: 1200px; overflow: hidden;
    background: var(--backdrop);
    font-family: "Lato", sans-serif;
  }
  .business-card {
    position: absolute; left: 80px; top: 298px;
    width: 1040px; height: 604px;
    background: var(--card);
    border-radius: 48px;
    overflow: hidden;
    box-shadow: 0 14px 30px rgba(0,0,0,0.35);
  }
  .name-tab {
    position: absolute; left: 0; top: 132px;
    width: 11px; height: 71px;
    background: var(--accent);
    border-radius: 0 5px 5px 0;
  }
  .holder-name {
    position: absolute; left: 34px; top: 122px;
    font-size: 38px; font-weight: 700; color: var(--accent);
  }
  .holder-title {
    position: absolute; left: 34px; top: 168px;
    font-size: 26px; color: var(--ink);
  }
  .brand {
    position: absolute; left: 730px; top: 80px;
    display: flex; align-items: center; gap: 16px;
  }
  .brand-dot {
    width: 96px; height: 96px; border-radius: 50%;
    background: var(--accent);
  }
  .brand-name {
    font-size: 36px; font-weight: 700; color: var(--ink);
    line-height: 1.05; width: 140px;
  }
  .personal-contact {
    position: absolute; left: 34px; top: 262px;
    list-style: none; font-size: 20px; color: var(--ink);
  }
  .personal-contact li { height: 39px; }
  .personal-contact .label { color: var(--accent); }
  .divider {
    position: absolute; left: 34px; top: 352px;
    width: 957px; height: 2px; background: var(--rule);
  }
  .office {
    position: absolute; top: 378px;
    font-size: 19.5px; color: var(--muted);
    line-height: 31px;
  }
  .office h3 {
    font-size: 23px; font-weight: 400; color: var(--accent);
    margin-bottom: 4px;
  }
  .office-head { left: 34px; }
  .office-dubai { left: 397px; }
  .office-qatar { left: 728px; top: 381px; }
  .footer-band {
    position: absolute; left: 0; bottom: 0;
    width: 1040px; height: 56px;
  }
  .website {
    position: absolute; left: 34px; bottom: 17px;
    font-size: 19px; color: #ffffff;
  }
</style>
</head>
<body>
  <div class="business-card">
    <div class="name-tab"></div>
    <h1 class="holder-name">Karim Delaroux</h1>
    <p class="holder-title">Managing Partner</p>

    <div class="brand">
      <span class="brand-dot"></span>
      <span class="brand-name">Tormin Group</span>
    </div>

    <ul class="personal-contact">
      <li><span class="label">Phone:</span> +971 (0)50 734 8162</li>
      <li><span class="label">Email:</span> karim@tormingroup.com</li>
    </ul>

    <div class="divider"></div>

    <section class="office office-head">
      <h3>Head Office</h3>
      <p>P.O. Box: 31842 Abu Dhabi. U.A.E</p>
      <p>Tel No: +971 (0)2 5718203</p>
      <p>Fax No: +971(0)2 5718204</p>
      <p>Email: sales@tormingroup.com</p>
    </section>
    <section class="office office-dubai">
      <h3>Dubai Office</h3>
      <p>P.O. Box: 470216 Dubai, U.A.E</p>
      <p>Tel No: +971 (0)4 582347</p>
      <p>Fax No: +971(0)4 582398</p>
      <p>Email: sales@tormingroup.com</p>
    </section>
    <section class="office office-qatar">
      <h3>Qater Office</h3>
      <p>P.O. Box: 20973 Doha, Qatter</p>
      <p>Tel No: +974 44317058</p>
      <p>Fax No: +971 44936172</p>
      <p>Email: sales@tormingroup.com</p>
    </section>

    <svg class="footer-band" viewBox="0 0 1040 56" aria-hidden="true">
      <polygon points="358,26 1040,26 1040,56 376,56" fill="var(--band)"/>
      <path d="M0,0 H300 Q330,0 344,22 L365,56 H0 Z" fill="var(--accent)"/>
    </svg>
    <span class="website">www.tormingroup.com</span>
  </div>
</body>
</html>
```